Modern looking signage for dental office.

Exterior signage for passing cars
Updates
Need extra days to review
Target Market(s)
Cars passing by
Font styles to use
Sans Serif
Colors
3276b5
Requirements
Must have
- Logo
- OPEN ON SUTURDAY AND SUNDAY
- NIGHT CLINIC AVAILABLE
- PLEASE USE THE FONT TYPE IN FILE 4 UPLOADED BELOW.
- (847) 302-7469
- Modern looking

```html
<!DOCTYPE html>
<html lang="en">
<head>
<meta charset="utf-8">
<title>Bright Peak Dental – Exterior Sign</title>
<link rel="stylesheet" href="https://fonts.googleapis.com/css2?family=Montserrat:wght@400;500;800;900&display=swap">
<style>
  :root {
    --page-bg: #e4e4e4;
    --sign-white: #ffffff;
    --header-fade: #eeeeee;
    --band-black: #0d0d0d;
    --brand-teal: #0c7a91;
    --divider: #8fc0cb;
    --logo-grey: #4a4a4c;
    --footer-grey: #dcdcdc;
    --ink: #000000;
    --text-white: #ffffff;
  }
  * { margin: 0; padding: 0; box-sizing: border-box; }
  html, body {
    width: 1200px; height: 1000px; overflow: hidden;
    background: var(--page-bg);
    font-family: "Montserrat", Arial, sans-serif;
  }
  .sign {
    position: absolute; left: 190px; top: 90px;
    width: 820px; height: 820px;
    background: var(--sign-white);
    overflow: hidden;
  }
  .sign-header {
    position: absolute; left: 0; top: 0; width: 100%; height: 222px;
    background: linear-gradient(to bottom, var(--sign-white) 55%, var(--header-fade));
  }
  .brand-mark {
    position: absolute; left: 76px; top: 40px;
    width: 142px; height: 142px; border-radius: 50%;
    border: 2px solid var(--logo-grey);
  }
  .brand-name {
    position: absolute; left: 236px; top: 88px;
    font-size: 44px; font-weight: 400; letter-spacing: 0;
    line-height: 1; color: var(--logo-grey); white-space: nowrap;
  }
  .brand-tagline {
    position: absolute; left: 284px; top: 162px;
    font-size: 23px; font-weight: 500; letter-spacing: 0.3px;
    line-height: 1; color: var(--logo-grey); white-space: nowrap;
  }
  .band { position: absolute; left: 0; width: 100%; background: var(--band-black); }
  .band-top { top: 222px; height: 10px; }
  .band-top-thin { top: 236px; height: 3px; }
  .band-bottom-thin { top: 681px; height: 3px; }
  .band-bottom { top: 688px; height: 10px; }
  .offer-panel {
    position: absolute; left: 0; top: 242px; width: 100%; height: 436px;
    background: var(--brand-teal); color: var(--text-white);
  }
  .offer {
    position: absolute; font-weight: 800; line-height: 1; white-space: nowrap;
  }
  .offer-centered { left: 0; width: 100%; text-align: center; }
  .offer-open { left: 170px; top: 27px; font-size: 112px; }
  .offer-days { top: 143px; font-size: 55px; }
  .offer-night { left: 115px; top: 254px; font-size: 90px; }
  .offer-available { top: 345px; font-size: 75px; }
  .offer-divider {
    position: absolute; left: 176px; top: 232px; width: 470px; height: 2px;
    background: var(--divider);
  }
  .tooth-icon {
    position: absolute; border-radius: 14px;
    background: rgba(255, 255, 255, 0.22);
  }
  .tooth-icon-open { left: 72px; top: 36px; width: 80px; height: 90px; }
  .tooth-icon-night { left: 35px; top: 266px; width: 65px; height: 75px; }
  .contact-bar {
    position: absolute; left: 0; top: 698px; width: 100%; height: 122px;
    background: var(--footer-grey);
  }
  .contact-icon { position: absolute; left: 105px; top: 27px; width: 68px; height: 68px; }
  .contact-phone {
    position: absolute; left: 197px; top: 20px;
    font-size: 70px; font-weight: 900; line-height: 1;
    color: var(--ink); white-space: nowrap;
  }
</style>
</head>
<body>
  <main class="sign">
    <header class="sign-header">
      <div class="brand-mark"></div>
      <div class="brand-name">BRIGHT PEAK DENTAL</div>
      <div class="brand-tagline">MODERN GENERAL DENTISTRY</div>
    </header>

    <div class="band band-top"></div>
    <div class="band band-top-thin"></div>

    <section class="offer-panel">
      <div class="tooth-icon tooth-icon-open" role="img" aria-label="Tooth outline icon"></div>
      <div class="offer offer-open">OPEN ON</div>
      <div class="offer offer-centered offer-days">SATURDAY AND SUNDAY</div>
      <div class="offer-divider"></div>
      <div class="tooth-icon tooth-icon-night" role="img" aria-label="Tooth outline icon"></div>
      <div class="offer offer-night">NIGHT CLINIC</div>
      <div class="offer offer-centered offer-available">AVAILABLE</div>
    </section>

    <div class="band band-bottom-thin"></div>
    <div class="band band-bottom"></div>

    <footer class="contact-bar">
      <svg class="contact-icon" viewBox="0 0 70 70" aria-hidden="true">
        <circle cx="35" cy="35" r="31" fill="none" stroke="var(--brand-teal)" stroke-width="6"/>
        <circle cx="35" cy="35" r="24" fill="var(--brand-teal)"/>
        <path d="M26 22c2-1 4 0 5 2l2 5c0 2-1 3-3 4 1 4 4 7 8 8 1-2 2-3 4-3l5 2c2 1 3 3 2 5-1 3-4 5-7 4-9-2-16-9-18-18-1-3 0-6 2-9z" fill="#ffffff"/>
        <path d="M40 22a9 9 0 0 1 8 8M40 27a4 4 0 0 1 3 3" fill="none" stroke="#ffffff" stroke-width="2" stroke-linecap="round"/>
      </svg>
      <div class="contact-phone">(847) 302-7469</div>
    </footer>
  </main>
</body>
</html>
```